Bookcover: Ways to Turn Into a Bold Pathfinder

I am publishing a super-low-cost innovation book for €4,99 on Quillmere Open Press to help everyone become a great innovator: young ambitious people without college education nor a big budget. Do you want to help me?

Brief:
Design a book cover 1600 x 2560 pixels for QOP.
Main title: Ways to Turn Into a Bold Pathfinder
Sub title: mindset - insights - skills & tools
Author: Joost ter Brakel
Design: captive, and appealing to everyone
Target Group: young ambitious people without college education

For quillmere please format the height/width ratio of 1.6:1

```html
<!DOCTYPE html>
<html lang="en">
<head>
<meta charset="utf-8">
<title>Ways to Turn Into a Bold Pathfinder — Book Cover</title>
<link rel="stylesheet" href="https://fonts.googleapis.com/css2?family=Bebas+Neue&family=Roboto:wght@500&display=swap">
<style>
  :root {
    --page-bg: #ffffff;
    --cover-blue: #3d43a0;
    --band-red: #c00000;
    --title-white: #ffffff;
    --accent-yellow: #f9d56e;
  }
  html, body {
    margin: 0;
    padding: 0;
    width: 1200px;
    height: 1200px;
    overflow: hidden;
    background: var(--page-bg);
  }
  .stage {
    position: relative;
    width: 1200px;
    height: 1200px;
  }
  .book-cover {
    position: absolute;
    left: 295px;
    top: 141px;
    width: 618px;
    height: 925px;
    display: block;
  }
  .cover-ground { fill: var(--cover-blue); }
  .title-band { fill: var(--band-red); stroke: var(--title-white); stroke-width: 2.5; stroke-linejoin: round; }
  .title-line {
    font-family: "Bebas Neue", "Oswald", sans-serif;
    fill: var(--title-white);
  }
  .subtitle {
    font-family: "Roboto", "Helvetica Neue", Arial, sans-serif;
    font-weight: 500;
    font-size: 52px;
    fill: var(--title-white);
  }
  .author {
    font-family: "Bebas Neue", "Oswald", sans-serif;
    font-size: 72px;
    fill: var(--title-white);
  }
  .author-surname { fill: var(--accent-yellow); }
  .idea-illustration { fill: url(#ideaTones); }
</style>
</head>
<body>
<div class="stage">
  <svg class="book-cover" viewBox="0 0 618 925" xmlns="http://www.w3.org/2000/svg" aria-label="Book cover: Ways to Turn Into a Bold Pathfinder by Joost ter Brakel">
    <defs>
      <linearGradient id="ideaTones" x1="0" x2="0" y1="0" y2="1">
        <stop offset="0%" stop-color="#e8bf2e"/>
        <stop offset="70%" stop-color="#d9aa22"/>
        <stop offset="100%" stop-color="#9a9a9a"/>
      </linearGradient>
    </defs>

    <rect class="cover-ground" x="0" y="0" width="618" height="925"/>

    <text class="title-line" x="33" y="143" font-size="158" textLength="355" lengthAdjust="spacingAndGlyphs">WAYS TO</text>
    <text class="title-line" x="33" y="257" font-size="158" textLength="500" lengthAdjust="spacingAndGlyphs">TURN INTO A</text>
    <text class="title-line" x="33" y="418" font-size="210" textLength="330" lengthAdjust="spacingAndGlyphs">BOLD</text>

    <rect class="idea-illustration" x="408" y="275" width="137" height="153" rx="10"
          role="img" aria-label="Illustration: crumpled yellow paper light bulb with metal socket and short rays"/>

    <path class="title-band" d="M-2 443 L30 440 L70 444 L110 439 L150 443 L190 440 L230 444 L270 439 L310 443 L350 440 L390 444 L430 439 L470 443 L510 440 L550 444 L590 440 L620 443
                              V610 L585 613 L545 609 L505 613 L465 609 L425 614 L385 609 L345 613 L305 609 L265 614 L225 609 L185 613 L145 609 L105 613 L65 609 L40 606 L20 612 L-2 613 Z"/>
    <text class="title-line" x="33" y="590" font-size="167" textLength="542" lengthAdjust="spacingAndGlyphs">PATHFINDER</text>

    <text class="subtitle" x="33" y="702" textLength="545" lengthAdjust="spacingAndGlyphs">MINDSET - INSIGHTS -</text>
    <text class="subtitle" x="33" y="757">SKILLS &amp; TOOLS</text>

    <text class="author" x="33" y="874" textLength="373" lengthAdjust="spacingAndGlyphs">JOOST TER <tspan class="author-surname">BRAKEL</tspan></text>
  </svg>
</div>
</body>
</html>
```